Slide Master for Holloway Engines - A Systematic Hedge Fund

We are looking for someone to produce a theme and slide master for us for our investor presentations. I have uploaded a few examples of templates that we would like to have included:
Main Title
Section Title
Slides with just bullet points
Different image/table configurations with bullet points and foot notes
Biographies of different lengths
A disclaimer (no one will read this but it should still look nice and needs to be in the presentations)
I have also uploaded the company logo, business card and colour definitions. Currently we have a blue colour scheme defined, but it would be nice to get a complementary set of colours so that when we have charts with more elements we can just draw from those.
The most important thing is that the slide master must be of general use to us. We arn't looking to have a specific presentation designed for us, but a theme/style that we can apply ourselves to any presentation we need to give in the future. It should have clearly defined guidelines for where content should go (and if this is different with and without footnotes for example). We would also like it to have a similar feel to the logo/business cards, so matt colours, high contrast, but not busy.
I'm excited to see the results!

```html
<!DOCTYPE html>
<html lang="en">
<head>
<meta charset="utf-8">
<title>Holloway Engines – Slide Master Sheet 3</title>
<link href="https://fonts.googleapis.com/css2?family=Roboto:wght@300;400;700&family=Arimo:wght@400;700&display=swap" rel="stylesheet">
<style>
:root{
  --board:#e6e6e6;
  --slide:#ffffff;
  --navy:#0d3d6b;
  --accent:#5b8fd0;
  --ink:#222831;
  --muted:#b5b9be;
  --rule:#c9cdd2;
  --series-a:#0d3d6b;
  --series-b:#9cc3a6;
}
*{box-sizing:border-box;margin:0;padding:0}
html,body{width:1200px;height:724px;overflow:hidden;background:var(--board)}
body{position:relative;font-family:'Roboto',sans-serif;font-weight:300;color:var(--ink)}
.slide{position:absolute;width:544px;height:306px;background:var(--slide);overflow:hidden}
.s9{left:39px;top:40px}.s10{left:617px;top:40px}
.s11{left:39px;top:377px}.s12{left:617px;top:377px}
.title{position:absolute;left:29px;top:31px;font-size:18.5px;font-weight:300;color:var(--navy);letter-spacing:-.1px}
.title b{font-weight:700}
.section{position:absolute;right:31px;top:45px;font-size:10px;color:var(--muted);letter-spacing:.2px}
.rule{position:absolute;left:29px;right:29px;top:56px;height:1px;background:var(--rule)}
.bullets{position:absolute;list-style:none;font-size:9px;line-height:11px;color:var(--ink)}
.bullets li{position:relative;padding-left:13px;margin-bottom:5.5px;width:115px}
.bullets li::before{content:"";position:absolute;left:0;top:3px;width:3px;height:3px;border-radius:50%;background:var(--accent)}
.foot-rule{position:absolute;left:0;top:272px;width:129px;height:1px;background:var(--rule)}
.footnote{position:absolute;left:10px;top:278px;width:285px;font-size:4.3px;line-height:6.2px;color:#9aa0a6}
.brand{position:absolute;right:22px;top:293px;font-size:5px;font-weight:700;color:var(--navy);display:flex;align-items:center;gap:3px}
.brand i{display:block;width:4px;height:4px;border-radius:50%;background:var(--accent)}
.page{position:absolute;right:10px;top:293px;font-size:5.5px;color:var(--ink);font-weight:400}
.data{position:absolute;left:28px;top:105px;border-collapse:collapse;font-family:'Arimo',sans-serif;font-size:5px;color:#111}
.data th,.data td{border:.7px solid #333;vertical-align:top;padding:2px 3px;text-align:left}
.data th{font-weight:700;text-align:center;height:21px;vertical-align:middle;line-height:6px}
.data td{height:14px}
.data tr.tall td{height:27px}
.chart-title{position:absolute;left:29px;top:83px;font-size:9px;font-weight:400;color:var(--accent)}
.chart{position:absolute;left:0;top:0}
.chart text{font-family:'Roboto',sans-serif;font-size:4px;fill:#666}
.name{position:absolute;left:29px;top:80px;font-size:12px;font-weight:400;color:#111}
.role{position:absolute;left:29px;top:98px;font-size:9px;color:var(--accent)}
.bio{position:absolute;font-size:8.5px;line-height:10.2px;text-align:justify;color:var(--ink)}
.bio-head{position:absolute;font-size:9px;font-weight:400;color:var(--accent)}
.sheet-no{position:absolute;right:14px;top:674px;font-size:38px;font-weight:700;color:#7d7d7d}
</style>
</head>
<body>

<section class="slide s9">
  <h1 class="title">Sub-heading <b>Tittle*</b></h1>
  <span class="section">SECTION TITTLE</span>
  <div class="rule"></div>
  <table class="data">
    <colgroup><col style="width:60px"><col style="width:23px"><col style="width:36px"><col style="width:31px"><col style="width:31px"><col style="width:39px"><col style="width:33px"><col style="width:69px"></colgroup>
    <tr><th>purchase<br>_time</th><th>sales<br>_id</th><th>customer<br>_id</th><th>currency</th><th>amount<br>_paid</th><th>device</th><th>has<br>_discount</th><th>agent_comment</th></tr>
    <tr><td>2018-01-01 8:48:00</td><td>466</td><td>1234</td><td>USD</td><td>$98.23</td><td>mobile app</td><td>FALSE</td><td></td></tr>
    <tr class="tall"><td>2018-01-01 9:15:00</td><td>467</td><td>3485</td><td>USD</td><td>$34.35</td><td>desktop</td><td>TRUE</td><td>out of stock in blue - accepted switch to green for a 5% discount</td></tr>
    <tr><td>2018-01-01 15:12:00</td><td>468</td><td>875</td><td>USD</td><td>$34.35</td><td>mobile web</td><td>FALSE</td><td></td></tr>
    <tr><td>2018-01-01 16:48:00</td><td>469</td><td>875</td><td>USD</td><td>$34.35</td><td>desktop</td><td>FALSE</td><td></td></tr>
    <tr><td>2018-01-01 18:09:00</td><td>470</td><td>5246</td><td>USD</td><td>$34.35</td><td>mobile web</td><td>FALSE</td><td></td></tr>
    <tr><td>2018-01-01 18:33:00</td><td>471</td><td>9872</td><td>USD</td><td>$34.35</td><td>mobile web</td><td>FALSE</td><td></td></tr>
    <tr><td>2018-01-02 7:25:00</td><td>472</td><td>2498</td><td>USD</td><td>$34.35</td><td>desktop</td><td>FALSE</td><td></td></tr>
    <tr><td>2018-01-02 8:01:00</td><td>473</td><td>7892</td><td>USD</td><td>$34.35</td><td>desktop</td><td>FALSE</td><td></td></tr>
  </table>
  <ul class="bullets" style="left:368px;top:126px">
    <li>Lorem ipsum dolor sit amet, consectetura dipiscing elit</li>
    <li>Lorem ipsum dolor sit amet, consectetura dipiscing elit</li>
    <li>Lorem ipsum dolor sit amet, consectetura dipiscing elit</li>
  </ul>
  <div class="foot-rule"></div>
  <p class="footnote">* Lorem ipsum dolor sit amet, consectetur adipiscing elit. Vestibulum lacinia eros eu pharetra mollis. Nullam vulputate purus mi, sed maximus est sodales mollis. Mauris nec vulputate eros. Cras lectus lacus, lacinia eu dapibus ac, tincidunt eu nisi. Suspendisse in volutpat risus. Nunc pharetra porttitor lorem.</p>
  <span class="brand"><i></i>Holloway Engines</span>
  <span class="page">9</span>
</section>

<section class="slide s10">
  <h1 class="title">Sub-heading <b>Tittle*</b></h1>
  <span class="section">SECTION TITTLE</span>
  <div class="rule"></div>
  <h2 class="chart-title">Chart Title with a Second Footnote<sup style="font-size:5px">*</sup></h2>
  <svg class="chart" width="544" height="306" viewBox="0 0 544 306" role="img" aria-label="Line chart of two rising series, 2010 to 2021">
    <g text-anchor="end">
      <text x="46" y="110">6.E+07</text><text x="46" y="125">5.E+07</text><text x="46" y="140">5.E+07</text>
      <text x="46" y="155">4.E+07</text><text x="46" y="170">4.E+07</text><text x="46" y="185">3.E+07</text>
      <text x="46" y="200">3.E+07</text><text x="46" y="215">2.E+07</text><text x="46" y="230">2.E+07</text>
      <text x="46" y="244">1.E+07</text>
    </g>
    <g text-anchor="middle"><text x="50" y="250">2010</text><text x="113" y="250">2013</text><text x="175" y="250">2016</text><text x="238" y="250">2019</text></g>
    <path d="M50 108V242H285" fill="none" stroke="#333" stroke-width=".6"/>
    <polyline fill="none" stroke="var(--series-b)" stroke-width="1.4" points="50,225 56,223 62,219 70,215 78,211 86,204 92,198 100,197 108,192 114,189 120,185 128,180 134,176 140,173 148,170 156,168 164,165 170,162 176,158 182,152 188,148 194,141 200,136 206,131 212,128 218,126 224,127 230,126 236,124 242,121 248,123 254,121 262,120 270,118 278,115 284,114"/>
    <polyline fill="none" stroke="var(--series-a)" stroke-width="1.2" points="50,226 56,224 62,220 70,216 78,212 86,206 92,201 100,200 108,195 114,194 120,189 128,184 134,180 140,177 148,174 156,172 164,169 170,165 176,160 182,154 188,150 194,143 200,138 206,133 212,130 218,128 224,129 230,128 236,126 242,122 248,124 254,122 262,121 270,119 278,116 284,115"/>
  </svg>
  <ul class="bullets" style="left:324px;top:117px">
    <li>Lorem ipsum dolor sit amet, consectetura dipiscing elit</li>
    <li>Lorem ipsum dolor sit amet, consectetura dipiscing elit</li>
    <li>Lorem ipsum dolor sit amet, consectetura dipiscing elit</li>
  </ul>
  <div class="foot-rule"></div>
  <p class="footnote">* Lorem ipsum dolor sit amet, consectetur adipiscing elit. Vestibulum lacinia eros eu pharetra mollis. Nullam vulputate purus mi, sed maximus est sodales mollis. Mauris nec vulputate eros. Cras lectus lacus, lacinia eu dapibus ac, tincidunt eu nisi. Suspendisse in volutpat risus. Nunc pharetra porttitor lorem.</p>
  <span class="brand"><i></i>Holloway Engines</span>
  <span class="page">10</span>
</section>

<section class="slide s11">
  <h1 class="title">Heading for <b>Biography</b></h1>
  <div class="rule"></div>
  <h2 class="name">Name</h2>
  <p class="role">Tittle</p>
  <p class="bio" style="left:109px;top:82px;width:149px">Lorem ipsum dolor sit amet, consectetur adipiscing elit. Vestibulum lacinia eros eu pharetra mollis. Nullam vulputate purus mi, sed maximus est sodales mollis. Mauris nec vulputate eros. Cras lectus lacus, lacinia eu dapibus ac, tincidunt eu nisi. Suspendisse in volutpat risus. Nunc pharetra porttitor lorem. Vivamus at lectus sit amet lacus dictum tincidunt at vel magna. Donec blandit nulla ac erat condimentum, fringilla feugiat ex porttitor. Proin est odio, suscipit vitae magna at, bibendum tincidunt mi. Aenean facilisis pharetra lacus sed tempus. Nam finibus eu diam eu consectetur.</p>
  <p class="bio" style="left:273px;top:83px;width:149px">Lorem ipsum dolor sit amet, consectetur adipiscing elit. Vestibulum lacinia eros eu pharetra mollis. Nullam vulputate purus mi, sed maximus est sodales mollis. Mauris nec vulputate eros. Cras lectus lacus, lacinia eu dapibus ac, tincidunt eu nisi. Suspendisse in volutpat risus. Nunc pharetra porttitor lorem. Vivamus at lectus sit amet lacus dictum tincidunt at vel magna. Donec blandit nulla ac erat condimentum, fringilla feugiat ex porttitor. Proin est odio, suscipit vitae magna at, bibendum tincidunt mi. Aenean facilisis pharetra lacus sed tempus. Nam finibus eu diam eu consectetur.</p>
  <span class="brand"><i></i>Holloway Engines</span>
  <span class="page">11</span>
</section>

<section class="slide s12">
  <h1 class="title">Heading for <b>Biography</b></h1>
  <div class="rule"></div>
  <h2 class="bio-head" style="left:29px;top:81px">Name, Tittle</h2>
  <p class="bio" style="left:29px;top:97px;width:161px">Lorem ipsum dolor sit amet, consectetur adipiscing elit. Vestibulum lacinia eros eu pharetra mollis. Nullam vulputate purus mi, sed maximus est sodales mollis. Mauris nec vulputate eros. Cras lectus lacus, lacinia eu dapibus ac, tincidunt eu nisi. Suspendisse in volutpat risus. Nunc pharetra porttitor lorem. Vivamus at lectus sit amet lacus dictum tincidunt at vel magna. Donec blandit nulla ac erat condimentum, fringilla feugiat ex porttitor. Proin est odio, suscipit vitae magna at, bibendum tincidunt mi. Aenean facilisis pharetra lacus sed tempus. Nam finibus eu diam eu consectetur.</p>
  <h2 class="bio-head" style="left:209px;top:81px">Name, Tittle</h2>
  <p class="bio" style="left:209px;top:97px;width:161px">Lorem ipsum dolor sit amet, consectetur adipiscing elit. Vestibulum lacinia eros eu pharetra mollis. Nullam vulputate purus mi, sed maximus est sodales mollis. Mauris nec vulputate eros. Cras lectus lacus, lacinia eu dapibus ac, tincidunt eu nisi. Suspendisse in volutpat risus. Nunc pharetra porttitor lorem. Vivamus at lectus sit amet lacus dictum tincidunt at vel magna. Donec blandit nulla ac erat condimentum, fringilla feugiat ex porttitor. Proin est odio, suscipit vitae magna at, bibendum tincidunt mi. Aenean facilisis pharetra lacus sed tempus. Nam finibus eu diam eu consectetur.</p>
  <span class="brand"><i></i>Holloway Engines</span>
  <span class="page">12</span>
</section>

<span class="sheet-no">3</span>
</body>
</html>
```